Etiketten für Honig
Wir können nur volle Punktzahl geben. Roswitha ist selbst Ideenreich, wirklich nett und setzte unsere Ideen schnell und engagiert um. Hat echt Spass gemacht mit ihr zu arbeiten.
Zielgruppe
Es scheint Missverständnisse zu geben weshalb ich das Briefing wohl ändern muss.
see below for English translation
Wir sind eine kleine Imkerei, die von der Liebhaberei in den Nebenerwerb wechselt. Wir verkaufen verschiedene Sortenhonige und Honigzubereitungen (siehe Webseite) im vorwiegend ländlichen Raum des Münsterlandes.
Entsprechend unseres Standortes und unserer Kundschaft benötigen wir ein klassisch ländliches Design. Hierfür haben wir auch bereits ein Logo welches verwendet werden muss.
English
There seems to be some misunderstanding, so I guess I'll have to change the briefing.
We are a small apiary that changes from hobby to sideline. We sell different types of honey and honey preparations (e.g. honey with raspberry) in a predominantly rural area of the Münsterland (Muensterland).
According to our location and our clientele, we need a classic rural design. We already have a logo which must be used.
Aufgabenstellung
Wir möchten ein rechteckiges Etikett mit Gewährverschluss das für verschiedene Sorten adoptierbar ist. Zum Beispiel durch den Austausch der Sortenbezeichnung und eine farbliche Veränderung.
Das Design soll später auf Naturpapier oder Graspapier gedruckt werden. Das Logo muss auf Etikett und Gewährverschluss abgebildet werden.
We would like a rectangular label with a guarantee seal that is adoptable for different varieties. For example, by exchanging the variety designation and changing the color.
The design will later be printed on uncoated paper or grass paper. The logo must be shown on the label and guarantee seal.

```html
<!DOCTYPE html>
<html lang="de">
<head>
<meta charset="utf-8">
<title>Honigmanufaktur Kessler – Etikett</title>
<link rel="stylesheet" href="https://fonts.googleapis.com/css2?family=Roboto+Condensed:wght@400&display=swap">
<style>
  :root {
    --backdrop: #eddcd0;
    --label-paper: #f3f3f3;
    --label-edge: #e2e2e2;
    --ink-body: #5a5a5a;
    --ink-brand: #5b5b5b;
    --leaf-green: #7cb342;
    --foliage-dark: #2f7a22;
    --foliage-mid: #4f9a2e;
    --foliage-light: #86c04a;
  }
  html, body {
    margin: 0;
    padding: 0;
    width: 1200px;
    height: 1200px;
    overflow: hidden;
    background: var(--backdrop);
  }
  .canvas {
    position: relative;
    width: 1200px;
    height: 1200px;
  }
  .label {
    position: absolute;
    left: 100px;
    top: 275px;
    width: 1000px;
    height: 650px;
    background: linear-gradient(90deg, #ececec 0%, var(--label-paper) 12%, #f6f6f6 50%, var(--label-paper) 88%, #ececec 100%);
    border-top: 6px solid #1c1c1c;
    box-sizing: border-box;
    overflow: hidden;
    font-family: "Roboto Condensed", "Arial Narrow", sans-serif;
    color: var(--ink-body);
  }
  .info-column {
    position: absolute;
    font-size: 14.5px;
    line-height: 1.02;
    margin: 0;
  }
  .info-column p { margin: 0 0 13px; }
  .info-column--left {
    left: 59px;
    top: 105px;
    width: 170px;
    text-align: left;
  }
  .info-column--right {
    left: 832px;
    top: 105px;
    width: 148px;
    text-align: right;
  }
  .brand-mark {
    position: absolute;
    left: 420px;
    top: 82px;
    width: 200px;
    height: 200px;
    border: 6px solid var(--leaf-green);
    border-radius: 50%;
    box-sizing: border-box;
  }
  .brand-name {
    position: absolute;
    left: 300px;
    top: 318px;
    width: 440px;
    text-align: center;
    color: var(--ink-brand);
    font-weight: 400;
    line-height: 1;
  }
  .brand-name__kind {
    display: block;
    font-size: 31px;
    letter-spacing: 1px;
  }
  .brand-name__house {
    display: block;
    font-size: 84px;
    margin-top: 2px;
  }
  .foliage {
    position: absolute;
    left: 0;
    bottom: 0;
    width: 1000px;
    height: 330px;
  }
</style>
</head>
<body>
<main class="canvas">
  <section class="label">
    <div class="info-column info-column--left">
      <p>"Lorem ipsum dolor sit amet, consectetur adipiscing elit, sed do eiusmod tempor.</p>
      <p>Ut enim ad minim veniam, quis nostrud exercitation</p>
      <p>Duis aute irure dolor in reprehenderit in voluptate velit esse cillum dolore eu</p>
    </div>

    <div class="brand-mark" aria-hidden="true"></div>
    <h1 class="brand-name">
      <span class="brand-name__kind">HONIGMANUFAKTUR</span>
      <span class="brand-name__house">Kessler</span>
    </h1>

    <div class="info-column info-column--right">
      <p>"Lorem ipsum dolor sit amet, consectetur adipiscing elit, sed do eiusmod tempor incididunt ut labore et dolore magna aliqua. Ut enim ad minim veniam, quis nostrud exercitation ullamco laboris nisi ut aliquip ex ea commodo consequat.</p>
      <p>Duis aute irure dolor in reprehenderit in voluptate velit esse cillum dolore eu fugiat nulla pariatur. Excepteur sint occaecat</p>
    </div>

    <svg class="foliage" viewBox="0 0 1000 330" role="img" aria-label="Border of green leaves, vines and small white and red meadow flowers along the bottom of the label">
      <defs>
        <linearGradient id="foliage-fill" x1="0" y1="0" x2="0" y2="1">
          <stop offset="0" stop-color="var(--foliage-light)"/>
          <stop offset="0.45" stop-color="var(--foliage-mid)"/>
          <stop offset="1" stop-color="var(--foliage-dark)"/>
        </linearGradient>
      </defs>
      <path fill="url(#foliage-fill)" d="M0 0 C20 40 30 120 60 150 C120 180 160 120 200 160 C260 170 300 140 340 160 C400 180 430 150 480 170 C540 180 570 150 620 150 C660 120 700 110 740 160 C790 170 840 120 880 130 C930 120 960 60 1000 20 L1000 330 L0 330 Z"/>
    </svg>
  </section>
</main>
</body>
</html>
```